eCommerce website for a DIY shop & communal center

We need a website for a business called The Maple Bench. The Maple Bench is both a shop and communal establishment where people with shared interests, especially in DIY (Do It Yourself) and crafting, can gather to shop for & work on projects while sharing ideas, equipment, supplies and knowledge. The shop is both brick & motor and online. The physical communal space provides workstations, equipment, tools and supplies and expertise for DIY lovers to create their projects.

Target Market(s)

Middle & upper class DIY enthusiasts, creative hobbyists, budding artists & small business owners

Industry/Entity Type

DIY, Arts & Crafts

Coding

Coded - Design and coding required

Number of Pages Required

5+ page

Requirements
Must have
• Menus to include 1. home page (with about us, operating hours, contacts, location, meet the team); 2. Bench activities (how to DIY at the Bench, booking, equipment & tools, house rules); 3. Bench events (events in the Bench, offsite events); 4. Resources (FAQs, tutorials, blogs, eBooks) and 5. Online shop
Nice to have
• Branding guidelines eg logo colours (see attachment) to influence design. Tillpost shop. Booking feature for activities & events at the Bench.

```html
<!DOCTYPE html>
<html lang="en">
<head>
<meta charset="utf-8">
<title>The Maple Bench – Tap into your crafty side</title>
<link href="https://fonts.googleapis.com/css2?family=Roboto:ital,wght@0,400;0,500;0,700;1,400;1,500&family=Great+Vibes&display=swap" rel="stylesheet">
<style>
:root{
  --orange:#f07a38;
  --orange-dark:#e2682a;
  --blue:#3d7fd6;
  --frame-blue:#2f8ee0;
  --ink:#222;
  --muted:#555;
  --footer:#121212;
  --white:#fff;
}
*{box-sizing:border-box;margin:0;padding:0}
html,body{width:1200px;height:4862px;overflow:hidden}
body{position:relative;background:var(--white);font-family:'Roboto',Arial,sans-serif;color:var(--ink)}
.abs{position:absolute}
.btn{position:absolute;display:flex;align-items:center;justify-content:center;background:var(--orange);color:var(--white);font-size:14px;font-weight:500;letter-spacing:.3px;border-radius:24px;text-transform:uppercase;box-shadow:0 3px 8px rgba(240,122,56,.3)}
.script{font-family:'Great Vibes',cursive;font-size:50px;font-weight:400;line-height:1}
.script .o{color:var(--orange)}
.script .b{color:var(--blue)}
.photo{position:absolute}

/* header */
.topbar-phone{left:100px;top:8px;display:flex;align-items:center;gap:12px;font-size:15px}
.icon-ring{width:32px;height:32px;border:1.5px solid #9aa;border-radius:50%;display:flex;align-items:center;justify-content:center}
.social-top{top:7px;display:flex;gap:10px;right:102px}
.social-top span{width:34px;height:34px;border:1.5px solid #7c8fa6;border-radius:50%;display:block}
.nav a{position:absolute;top:63px;font-size:14.5px;font-weight:500;color:#111;text-decoration:none;text-transform:uppercase}
.logo-tab{left:496px;top:0;width:208px;height:134px;background:var(--white);border-radius:0 0 104px 104px;display:flex;align-items:center;justify-content:center;z-index:3}
.logo-tab span{font-size:23px;font-weight:700;color:var(--orange);text-align:center;line-height:1.15}

/* hero */
.hero{left:0;top:100px;width:1200px;height:564px;background:linear-gradient(110deg,#7a6a60 0%,#b9aea4 30%,#d9d2c8 55%,#a99c8c 80%,#6a5c50 100%)}
.hero h1{position:absolute;left:102px;top:202px;font-size:53px;font-weight:700;line-height:1;color:var(--white);text-transform:uppercase;text-shadow:0 2px 6px rgba(0,0,0,.3)}
.dots{position:absolute;left:556px;top:526px;display:flex;gap:13px}
.dots i{width:12px;height:12px;border:1.5px solid var(--white);border-radius:50%;display:block}
.dots i.on{background:var(--white)}

/* how it works */
.center{left:0;width:1200px;text-align:center}
.lead{font-size:14px;color:var(--muted);line-height:1.85}
.step-frame{position:absolute;top:881px;width:192px;height:192px;border:3px solid var(--frame-blue)}
.step-blob{position:absolute;left:-4px;top:14px;width:212px;height:186px;border-radius:50% 48% 46% 52%}
.step-cap{position:absolute;top:1092px;width:245px;text-align:center}
.step-cap h3{font-size:14.5px;font-style:italic;font-weight:500;line-height:1.3}
.step-cap h3 em{color:var(--orange);font-style:italic}
.step-cap p{font-size:11.5px;color:var(--muted);line-height:1.75;margin-top:6px}

/* about */
.about{left:0;top:1387px;width:1200px;height:481px;background:linear-gradient(90deg,#8a4a2c,#a8603c 40%,#9c5434 70%,#7a3f24)}
.about-art{left:10px;top:1392px;width:620px;height:476px;background:radial-gradient(ellipse at 50% 55%,rgba(220,200,180,.55),rgba(160,90,60,0) 70%)}
.about-copy{left:659px;top:1480px;width:440px;color:var(--white)}
.about-copy .script{color:var(--white);font-size:48px}
.about-copy p{font-size:13.5px;line-height:2;margin-top:14px}
.about-copy p+p{margin-top:0}

/* featured */
.wash-blue{background:radial-gradient(ellipse at 50% 50%,rgba(110,185,230,.45),rgba(160,210,240,.2) 45%,rgba(255,255,255,0) 72%)}
.card-img{position:absolute;top:2095px;width:321px;height:368px}
.card-cap{position:absolute;top:2480px;width:321px;text-align:center;font-size:21px;font-weight:500}

/* hours */
.wash-peach{background:radial-gradient(ellipse at 55% 45%,rgba(246,160,120,.55),rgba(250,200,170,.3) 45%,rgba(255,255,255,0) 72%)}
.hours{left:240px;top:2745px;width:317px;text-align:right}
.hours ul{list-style:none;margin-top:22px}
.hours li{font-size:14.5px;line-height:29.5px;color:#222}

/* location */
.loc{left:642px;top:3250px;width:500px}
.loc ul{list-style:none;margin-top:12px}
.loc li{font-size:15px;line-height:29.5px;color:#222}
.loc a{color:#2a4fd8;text-decoration:underline}

/* team */
.member-img{position:absolute;top:3887px;width:321px;height:325px}
.member-name{position:absolute;top:4224px;width:321px;text-align:center}
.member-name b{display:block;font-size:21px;font-weight:500}
.member-name span{font-size:14px;color:var(--muted)}

/* footer */
.footer{left:0;top:4506px;width:1200px;height:356px;background:var(--footer);color:var(--white)}
.fcol{position:absolute;top:85px}
.fcol h4{font-size:15px;font-weight:500;text-transform:uppercase;letter-spacing:.3px;margin-bottom:12px}
.fcol li{list-style:none;font-size:13.5px;line-height:28.3px}
.email{position:absolute;left:843px;top:112px;width:257px;height:41px;background:var(--white);border-radius:20px;color:#333;font-size:12.5px;padding-left:16px;display:flex;align-items:center}
.sub{left:843px;top:163px;width:257px;height:41px;border-radius:20px;box-shadow:none}
.fsocial{position:absolute;top:225px;left:851px;display:flex;gap:8px}
.fsocial span{width:34px;height:34px;border-radius:50%;background:var(--white);display:block}
.copy{position:absolute;top:314px;left:0;width:1200px;text-align:center;font-size:12.5px}
</style>
</head>
<body>

<!-- header -->
<div class="abs topbar-phone">
  <span class="icon-ring">
    <svg width="15" height="15" viewBox="0 0 24 24"><path d="M6.6 10.8a15 15 0 0 0 6.6 6.6l2.2-2.2c.3-.3.7-.4 1-.2 1.1.4 2.3.6 3.6.6.6 0 1 .4 1 1V20c0 .6-.4 1-1 1A17 17 0 0 1 3 4c0-.6.4-1 1-1h3.5c.6 0 1 .4 1 1 0 1.3.2 2.5.6 3.6.1.3 0 .7-.2 1z" fill="#333"/></svg>
  </span>
  <span>0700 555 218</span>
</div>
<div class="abs social-top" aria-label="Social links"><span></span><span></span><span></span><span></span></div>
<nav class="nav">
  <a style="left:100px">Home</a>
  <a style="left:194px">Bench Activities</a>
  <a style="left:379px">Bench Events</a>
  <a style="left:704px">Resources</a>
  <a style="left:849px">Online Shop</a>
  <a style="left:1008px">Contact Us</a>
</nav>
<div class="abs logo-tab"><span>The Maple<br>Bench</span></div>

<!-- hero -->
<section class="abs hero" role="img" aria-label="Photo of the craft shop interior with pegboard walls of supplies and colourful chairs">
  <h1>Tap into your<br>crafty side!</h1>
  <div class="btn" style="left:102px;top:330px;width:178px;height:46px">Get Started</div>
  <div class="dots"><i></i><i class="on"></i><i></i><i></i></div>
</section>

<!-- how it works -->
<h2 class="abs center script" style="top:755px"><span class="o">How it</span> <span class="b">Works</span></h2>
<p class="abs center lead" style="top:814px">The following are the services offered by the Bench. Click on the links for more information</p>

<div class="step-frame" style="left:119px"><div class="step-blob" role="img" aria-label="Photo of a customer crafting at a pegboard wall" style="background:linear-gradient(135deg,#8a9aa8,#c7b6a4 50%,#4a4a52)"></div></div>
<div class="step-frame" style="left:373px"><div class="step-blob" role="img" aria-label="Photo of supplies and a laptop on a work table" style="background:linear-gradient(135deg,#e8e2da,#cfc3b5 50%,#9a8e80)"></div></div>
<div class="step-frame" style="left:632px"><div class="step-blob" role="img" aria-label="Photo of people making products at a workshop table" style="background:linear-gradient(135deg,#d0b090,#b87a5c 50%,#7a5a4a)"></div></div>
<div class="step-frame" style="left:889px"><div class="step-blob" role="img" aria-label="Photo of a string art piece held up at an event" style="background:linear-gradient(135deg,#c8a888,#9a5a40 50%,#6a3a2a)"></div></div>

<div class="step-cap" style="left:92px"><h3><em>1.</em> Crafting in the Bench</h3><p>Lorem ipsum dol, consectetdipiscing elit, sed do eiusmod temporcididunt ut labore et dolore maalQuis ipsum suspendisse ultrices gravida.</p></div>
<div class="step-cap" style="left:347px"><h3><em>2.</em> Sale of supplies and equipment</h3><p>Lorem ipsum dol, consectetdipiscing elit, sed do eiusmod temporcididunt ut labore et dolore maalQuis ipsum suspendisse ultrices gravida.</p></div>
<div class="step-cap" style="left:604px"><h3><em>3.</em> Sale of products made in the Bench under the brand Made by The Maple Bench</h3><p>Lorem ipsum dol, consectetdipiscing elit, sed do eiusmod temporcididunt</p></div>
<div class="step-cap" style="left:862px"><h3><em>4.</em> Holding events, both at the Bench and offsite</h3><p>Lorem ipsum dol, consectetdipiscing elit, sed do eiusmod temporcididunt ut labore et dolore maalQuis ipsum</p></div>

<div class="btn" style="left:509px;top:1245px;width:181px;height:48px">Book a Project</div>

<!-- about -->
<section class="abs about" role="img" aria-label="Brick wall backdrop"></section>
<div class="abs about-art" role="img" aria-label="Illustration of four smiling makers holding oversized tools: colour swatches, a drill, a hammer and scissors"></div>
<div class="abs about-copy">
  <h2 class="script">About Us</h2>
  <p>The Maple Bench is both a shop and communal establishment where people with shared interests, especially in DIY, can gather to shop for &amp; work on projects while sharing ideas, equipment, supplies and knowledge.</p>
  <p>This space, designed and dedicated to hands-on creativity, allows people to enter with an idea and leave with a complete project.</p>
  <p>DIY = Do-It-Yourself</p>
  <div class="btn" style="left:0;top:268px;width:181px;height:48px;position:absolute">Learn More</div>
</div>

<!-- featured projects -->
<div class="abs wash-blue" role="img" aria-label="Soft blue watercolour wash" style="left:0;top:2220px;width:1200px;height:420px"></div>
<h2 class="abs center script" style="top:1955px"><span class="o">Featured</span> <span class="b">Projects</span></h2>
<p class="abs center lead" style="top:2012px">Lorem ipsum dolor sit amet, consectetur adipiscing elit, sed do eiusmod tempor incididunt ut labore<br>et dolore magna aliqua. Quis ipsum suspendisse ultrices gravida.</p>

<div class="card-img" role="img" aria-label="Photo of a hanging trio of small red paintings on a branch" style="left:100px;background:linear-gradient(180deg,#eef0f0,#e2e4e4 60%,#c9cccc)"></div>
<div class="card-img" role="img" aria-label="Photo of a silhouette painting with a patterned headwrap and matching coasters" style="left:440px;background:linear-gradient(160deg,#f2efe8,#e6e0d4 55%,#cfc6b6)"></div>
<div class="card-img" role="img" aria-label="Photo of a painted wood slice with a sunset beach scene" style="left:779px;background:linear-gradient(160deg,#8a8f94,#c9b59a 45%,#e88a3a 65%,#4a5a6a)"></div>
<div class="card-cap" style="left:100px">Sed ut perspiciatis und</div>
<div class="card-cap" style="left:440px">Sed ut perspiciatis und</div>
<div class="card-cap" style="left:779px">Sed ut perspiciatis und</div>

<!-- operating hours -->
<div class="abs wash-peach" role="img" aria-label="Soft peach watercolour wash" style="left:60px;top:2700px;width:540px;height:420px"></div>
<div class="abs hours">
  <h2 class="script" style="font-size:46px"><span class="o">Operating</span> <span class="b">Hours</span></h2>
  <ul>
    <li>Nairobi:</li>
    <li>Monday - Saturday: 9am - 6pm</li>
    <li>Public holidays: 8am - 5pm</li>
    <li>Sunday: Closed</li>
    <li>Mombasa:</li>
    <li>Tuesday - Sunday: 10am - 7pm</li>
    <li>Public holidays: 10am - 7pm</li>
    <li>Monday: Closed</li>
  </ul>
</div>
<div class="photo" role="img" aria-label="Photo of a woman in ear defenders cutting timber on a mitre saw" style="left:600px;top:2723px;width:498px;height:413px;background:linear-gradient(135deg,#b4b8b8,#8a9aa8 40%,#3e5a7a 65%,#c9a878)"></div>

<!-- location -->
<div class="abs wash-blue" role="img" aria-label="Soft blue watercolour wash" style="left:560px;top:3200px;width:620px;height:320px"></div>
<div class="photo" role="img" aria-label="Photo of a modern two-storey shopfront building under a blue sky" style="left:100px;top:3221px;width:500px;height:412px;background:linear-gradient(180deg,#2a6ad0,#6aa2e8 45%,#d8c2a4 46%,#c4a884 80%,#7a7e80)"></div>
<div class="abs loc">
  <h2 class="script" style="font-size:46px"><span class="o">Our</span> <span class="b">Location</span></h2>
  <ul>
    <li>Nairobi:</li>
    <li>House 9, Ridgeview Court, Acacia Lane</li>
    <li>Hillside Mews, Greenbank</li>
    <li>Nairobi</li>
    <li><a>https://maps.example.com/maplebench-nairobi</a></li>
    <li>&nbsp;Mombasa:</li>
    <li>Within Harbour Grill, Next to Palm Shore Resort,<br>Coral Beach Road, Mombasa</li>
    <li><a>https://maps.example.com/maplebench-mombasa</a></li>
  </ul>
</div>
<div class="btn" style="left:634px;top:3583px;width:183px;height:48px">Contact Us</div>

<!-- team -->
<h2 class="abs center script" style="top:3722px"><span class="o">Meet Our Team</span></h2>
<p class="abs center lead" style="top:3782px;left:150px;width:900px">Sed ut perspiciatis unde omnis iste natus error sit voluptatem accusantium doloremque laudantium, totam rem aperiam, eaque ipsa quae ab illo inventore veritatis et quasi architecto beatae vitae dicta sunt explicabo. Nemo enim ipsam voluptatem quia voluptas sit aspernatur aut odit aut fugit, sed quia consequuntur magni dolores eos qui ratione voluptatem</p>

<div class="abs wash-blue" role="img" aria-label="Soft blue watercolour wash" style="left:0;top:4080px;width:1200px;height:340px"></div>
<div class="member-img" role="img" aria-label="Portrait photo of team member" style="left:100px;background:linear-gradient(180deg,#e6e6e6,#d8d8d8 60%,#a8c4e0)"></div>
<div class="member-img" role="img" aria-label="Portrait photo of team member" style="left:440px;background:linear-gradient(180deg,#3a6ab0,#5a8ac8 60%,#8aaed8)"></div>
<div class="member-img" role="img" aria-label="Portrait photo of team member" style="left:779px;background:linear-gradient(180deg,#e4e4e4,#d2d2d2 60%,#6a7a9a)"></div>
<div class="member-name" style="left:100px"><b>Daniel Reyes</b><span>CEO</span></div>
<div class="member-name" style="left:440px"><b>Marcus Hale</b><span>CEO</span></div>
<div class="member-name" style="left:779px"><b>Tom Ellison</b><span>CEO</span></div>
<div class="btn" style="left:506px;top:4289px;width:187px;height:46px">Meet Our Team</div>

<!-- footer -->
<footer class="abs footer">
  <div class="fcol" style="left:102px"><h4>About</h4><ul><li>Our Story</li><li>Press</li><li>Locations</li><li>Blog</li><li>Contact Us</li></ul></div>
  <div class="fcol" style="left:236px"><h4>Our Offering</h4><ul><li>Projects</li><li>Paint Room</li><li>Parties</li><li>Classes</li></ul></div>
  <div class="fcol" style="left:421px"><h4>Other</h4><ul><li>Franchise</li><li>Gift Cards</li><li>FAQ</li><li>Refund Policy</li></ul></div>
  <div class="fcol" style="left:572px"><h4>Contact Us</h4><ul><li>48 Timberline Way Northfield</li><li>40512</li><li>555 - 014 - 2290</li><li>hello@maplebench.example</li></ul></div>
  <div class="fcol" style="left:843px"><h4>Get Updates &amp; Promos</h4></div>
  <div class="email">Email Address</div>
  <div class="btn sub">Subscribe</div>
  <div class="fsocial" aria-label="Social links"><span></span><span></span><span></span><span></span></div>
  <p class="copy">Copyright © 2021 The Maple Bench. All rights reserved.</p>
</footer>

</body>
</html>
```